Business card design for holistic health care clinic

We need a double-sided business card design for our holistic health care clinic that integrates our logo design and also its color scheme. My business is called Valmira. It is an integrative medicine clinic. You have already done the logo for me. Please ensure an elegant and upscale design that is not cluttered, but still has all the necessary information (please see below for details).

Target Market(s)

Wellness, fitness, rehabilitation for educated, well-traveled open-minded clients who are focused on natural, organic, balanced and preventive healthcare and lifestyle.

Industry/Entity Type

Medical

Contact Information for Business Card

Modern, clean.

Number of Pages Required

1 page

Font styles to use
Serif
Sans Serif

Colors

Designer to choose colors to be used in the design.

Requirements
Must have
• Logo on one side, all other information on the other side.
• Other information should include:
• Tobias Wrenfeld - DOE, CPT, LMT
• 4100 East Marrow Drive
• Austin, TX 78119
• 512 555 0148
• 818 555 0192
• info@ValmiraHealth.example
• t.wrenfeld@ValmiraHealth.example
Nice to have
• Darker background on front - but not totally black - shaded/dark gray.

```html
<!DOCTYPE html>
<html lang="en">
<head>
<meta charset="utf-8">
<title>Valmira Business Card</title>
<link rel="stylesheet" href="https://fonts.googleapis.com/css2?family=Nunito:wght@800&family=Roboto:ital,wght@0,400;1,400&family=Roboto+Condensed:wght@700&display=swap">
<style>
  :root {
    --page-bg: #e3e3e3;
    --brand-blue: #0a92cf;
    --wave-dark: #2c2c2c;
    --card-white: #f4f4f4;
    --text-white: #ffffff;
    --text-gray: #4a4a4a;
    --rule-gray: #8a8a8a;
  }
  * { margin: 0; padding: 0; box-sizing: border-box; }
  html, body { width: 1200px; height: 960px; overflow: hidden; }
  body { background: var(--page-bg); position: relative; font-family: "Roboto", Arial, sans-serif; }

  .card {
    position: absolute;
    left: 313px;
    width: 600px;
    height: 343px;
    overflow: hidden;
    box-shadow: 0 2px 4px rgba(0,0,0,0.25);
  }
  .card-front { top: 113px; background: var(--brand-blue); }
  .card-back { top: 472px; background: var(--card-white); }

  .wave-art { position: absolute; inset: 0; width: 600px; height: 343px; }

  .contact-list {
    position: absolute;
    right: 40px;
    top: 37px;
    color: var(--text-white);
    font-size: 14px;
    line-height: 19px;
    text-align: right;
  }
  .contact-list .address { margin-bottom: 12px; }
  .contact-line { display: flex; justify-content: flex-end; align-items: center; gap: 8px; }
  .contact-line svg { width: 12px; height: 12px; flex: none; }

  .brand-name {
    font-family: "Nunito", Arial, sans-serif;
    font-weight: 800;
    color: var(--brand-blue);
    letter-spacing: 1px;
    line-height: 1;
  }
  .brand-descriptor {
    font-family: "Nunito", Arial, sans-serif;
    font-weight: 800;
    color: var(--brand-blue);
    line-height: 1;
  }

  .front-brand { position: absolute; left: 40px; top: 198px; }
  .front-brand .brand-name { font-size: 50px; }
  .front-brand .brand-descriptor { font-size: 14.5px; margin-top: 3px; margin-left: 4px; }

  .holder {
    position: absolute;
    left: 40px;
    top: 282px;
    font-family: "Roboto Condensed", Arial, sans-serif;
    font-weight: 700;
    color: var(--brand-blue);
    font-size: 20px;
  }
  .holder .credentials { font-size: 12.5px; }

  .back-brand { position: absolute; left: 0; right: 0; top: 128px; text-align: center; }
  .back-brand .brand-name { font-size: 62px; }
  .back-brand .brand-descriptor { font-size: 17px; margin-top: 4px; }

  .tagline {
    position: absolute;
    left: 90px;
    right: 90px;
    top: 284px;
    display: flex;
    align-items: center;
    gap: 8px;
    font-style: italic;
    font-size: 16px;
    color: var(--text-gray);
    white-space: nowrap;
  }
  .tagline::before, .tagline::after {
    content: "";
    flex: 1;
    height: 1px;
    background: linear-gradient(90deg, transparent, var(--rule-gray));
  }
  .tagline::after { background: linear-gradient(90deg, var(--rule-gray), transparent); }
</style>
</head>
<body>

<section class="card card-front">
  <svg class="wave-art" viewBox="0 0 600 343" aria-hidden="true">
    <path d="M0,48 C90,10 200,15 280,105 S440,250 600,242 L600,343 L0,343 Z" fill="var(--wave-dark)"/>
    <path d="M170,22 C225,30 255,60 290,110 S430,262 600,250" fill="none" stroke="var(--brand-blue)" stroke-width="3"/>
    <path d="M180,24 C238,36 268,66 302,118 S440,272 600,258" fill="none" stroke="var(--brand-blue)" stroke-width="3"/>
    <path d="M190,27 C250,42 282,74 314,124 S452,280 600,266" fill="none" stroke="var(--brand-blue)" stroke-width="3"/>
  </svg>

  <div class="contact-list">
    <p class="address">4100 East Marrow Drive<br>Austin, TX 78119</p>
    <p class="contact-line">512 555 0148
      <svg viewBox="0 0 12 12"><path d="M2.5 1 L4.5 1 L5.3 3.6 L4 4.6 C4.6 6 6 7.4 7.4 8 L8.4 6.7 L11 7.5 L11 9.5 C11 10.4 10.3 11 9.5 11 C5 11 1 7 1 2.5 C1 1.7 1.6 1 2.5 1 Z" fill="var(--text-white)"/></svg>
    </p>
    <p class="contact-line">818 555 0192
      <svg viewBox="0 0 12 12"><rect x="3" y="0.8" width="6" height="10.4" rx="1" fill="none" stroke="var(--text-white)" stroke-width="1.2"/><circle cx="6" cy="9.4" r="0.6" fill="var(--text-white)"/></svg>
    </p>
    <p class="contact-line">t.wrenfeld@ValmiraHealth.example
      <svg viewBox="0 0 12 12"><rect x="1" y="3" width="10" height="6.5" fill="var(--text-white)"/><path d="M1 3 L6 7 L11 3" fill="none" stroke="var(--brand-blue)" stroke-width="0.8"/></svg>
    </p>
    <p class="contact-line">www.ValmiraHealth.example
      <svg viewBox="0 0 12 12"><circle cx="6" cy="6" r="5" fill="var(--text-white)"/><path d="M3.5 3 L6 4 L5 6 L7 7.5 L6.5 10" fill="none" stroke="var(--brand-blue)" stroke-width="1"/></svg>
    </p>
  </div>

  <div class="front-brand">
    <p class="brand-name">Valmira</p>
    <p class="brand-descriptor">Integrative Holistic Medicine</p>
  </div>

  <p class="holder">Tobias Wrenfeld <span class="credentials">- DOE, CPT, LMT</span></p>
</section>

<section class="card card-back">
  <div class="back-brand">
    <p class="brand-name">Valmira</p>
    <p class="brand-descriptor">Integrative Holistic Medicine</p>
  </div>
  <p class="tagline">helping the body help itself</p>
</section>

</body>
</html>
```